Website redesign www.marigoldlawpc.com law firm site

Need to redesign the website that I currently have to look more modern and professional. Would also like to be able to make updates and post without having a huge hassle. See current www.marigoldlawpc.com. I just think that it looks very immature and it's very templated there's no ability for me to make posts or Add links or anything like that

Target Market(s)

California people looking for a powerhouse attorney in

Industry/Entity Type

Legal

Number of Pages Required

3 page

Font styles to use
Serif
Sans Serif

Colors
ec1f27
000000
ffffff

Requirements
Must have
• Must be mobile friendly. Must look professional and have ability to post links to other websites. Must have ability to post blogs or articles. Would like to be able to read my FeeTrove account and also have the ability to upload forms for people to download
Nice to have
• Simple design easy to use and not cluttered with too much text

```html
<!DOCTYPE html>
<html lang="en">
<head>
<meta charset="utf-8">
<title>Marigold Law, P.C. — Alder California Attorney</title>
<link rel="stylesheet" href="https://fonts.googleapis.com/css2?family=Raleway:wght@400;500;600;700&family=Open+Sans:wght@400;600;700&display=swap">
<style>
:root{
  --red:#ec1f27;
  --black:#000000;
  --white:#ffffff;
  --ink:#333333;
  --muted:#555555;
  --footer:#262626;
  --light:#f3f3f3;
  --line:#e2e2e2;
}
*{box-sizing:border-box;margin:0;padding:0}
html,body{width:1200px;height:2449px;overflow:hidden;background:var(--white)}
body{position:relative;font-family:"Open Sans",Arial,sans-serif;color:var(--ink)}
section,header,footer{position:absolute;left:0;width:1200px}

/* header */
.site-header{top:0;height:77px;background:var(--white);border-bottom:1px solid var(--line)}
.brand{position:absolute;left:152px;top:18px;width:142px;text-align:center;font-family:"Raleway",sans-serif;font-weight:600;font-size:22px;color:var(--red);line-height:26px;white-space:nowrap}
.brand small{display:block;font-size:11px;line-height:14px;border-top:1px solid var(--red);margin-top:2px}
.main-nav{position:absolute;left:0;top:29px;width:1000px;height:20px;font-size:12.5px;color:var(--ink)}
.main-nav a{position:absolute;top:0;color:inherit;text-decoration:none;white-space:nowrap}
.main-nav a.active{color:var(--red)}
.search-btn{position:absolute;left:1004px;top:21px;width:34px;height:34px;border-radius:50%;background:var(--red)}

/* hero */
.hero{top:77px;height:540px;background:linear-gradient(120deg,#2b2f36 0%,#4a4e55 35%,#6b6a68 55%,#3a3c40 100%)}
.hero-photo{position:absolute;inset:0}
.hero-content{position:absolute;left:0;width:1200px;top:196px;text-align:center;color:var(--white)}
.hero-content h1{font-family:"Raleway",sans-serif;font-weight:700;font-size:38px;line-height:46px}
.hero-content p{font-family:"Raleway",sans-serif;font-weight:500;font-size:18px;line-height:23px;margin-top:8px}
.btn{display:inline-block;background:var(--red);color:var(--white);font-family:"Open Sans",sans-serif;font-weight:600;font-size:12px;text-transform:uppercase;text-decoration:none}
.hero .btn{margin-top:20px;width:154px;height:39px;line-height:39px}
.slider-dots{position:absolute;top:483px;left:569px;display:flex;gap:3px}
.slider-dots span{width:14px;height:14px;border-radius:50%;background:var(--white);border:2px solid var(--white)}
.slider-dots span.off{background:transparent}

/* section titles */
.section-title{text-align:center;font-family:"Raleway",sans-serif;font-weight:500;font-size:22px;color:var(--black);letter-spacing:.5px}
.title-rule{position:absolute;left:480px;width:240px;height:1px;background:var(--red)}
.title-rule::after{content:"";position:absolute;left:100px;top:-1px;width:40px;height:3px;background:var(--red)}

/* practice areas */
.practice{top:617px;height:441px}
.practice .section-title{position:absolute;top:30px;width:1200px}
.practice .title-rule{top:69px}
.practice-intro{position:absolute;top:86px;left:225px;width:750px;text-align:center;font-size:10.5px;line-height:20px;color:var(--ink)}
.area{position:absolute;top:146px;width:210px;text-align:center}
.area-icon{display:block;margin:0 auto}
.area h3{font-family:"Open Sans",sans-serif;font-weight:400;font-size:14.5px;color:var(--ink);margin-top:14px}
.area p{font-size:11px;line-height:18.5px;margin-top:12px;color:var(--ink)}

/* about */
.about{top:1058px;height:436px;background:linear-gradient(100deg,#1e1d1c 0%,#2e2a27 45%,#3d3632 70%,#2a2624 100%)}
.about-media{position:absolute;left:162px;top:95px;width:334px;height:247px;background:var(--white);padding:22px 14px}
.about-media div{width:100%;height:100%;background:radial-gradient(ellipse at 50% 55%,#7a1a1a 0%,#a03a30 35%,#e6d9cf 75%,#ffffff 100%)}
.about-text{position:absolute;left:531px;top:96px;width:507px;color:var(--white)}
.about-text h2{font-family:"Raleway",sans-serif;font-weight:500;font-size:20px;line-height:31px;letter-spacing:.5px}
.about-text hr{border:0;height:1px;background:#bdbdbd;width:190px;margin:12px 0 19px}
.about-text p{font-size:10.5px;line-height:18.2px;color:#e8e8e8}

/* blog */
.blog{top:1494px;height:536px;background:var(--light)}
.blog .section-title{position:absolute;top:34px;width:1200px}
.blog .title-rule{top:73px}
.cards{position:absolute;left:162px;top:106px;display:flex;gap:16px}
.post{width:207px;height:376px;background:var(--white);border:1px solid var(--line)}
.post-thumb{height:153px}
.post-body{padding:12px 15px 0 15px}
.post h3{font-family:"Raleway",sans-serif;font-weight:500;font-size:16.5px;line-height:22px;color:var(--black)}
.post-meta{display:flex;gap:14px;font-size:9.5px;color:var(--red);margin-top:10px;font-weight:600}
.post-meta span{display:flex;align-items:center;gap:3px}
.post p{font-size:10.5px;line-height:17px;margin-top:12px;color:var(--ink)}
.post .btn{margin-top:14px;width:98px;height:34px;line-height:34px;text-align:center;font-size:10.5px}

/* partners */
.partners{top:2030px;height:114px;background:var(--white)}
.partner{position:absolute}

/* footer */
.site-footer{top:2144px;height:240px;background:var(--footer);color:#d9d9d9}
.foot-brand{position:absolute;left:167px;top:44px;width:192px;text-align:center;font-family:"Raleway",sans-serif;font-weight:600;font-size:28px;line-height:32px;color:var(--white);white-space:nowrap}
.foot-brand small{display:block;font-size:13px;line-height:16px;border-top:1px solid var(--white);margin-top:3px}
.foot-about{position:absolute;left:162px;top:108px;width:200px;font-size:10.5px;line-height:18px}
.foot-col{position:absolute;top:46px}
.foot-col h4{font-family:"Open Sans",sans-serif;font-weight:600;font-size:14px;color:var(--white);text-transform:uppercase}
.foot-col ul{list-style:none;margin-top:12px}
.foot-col li{font-size:10.5px;line-height:19.6px;display:flex;align-items:center;gap:8px;white-space:nowrap}
.foot-col li::before{content:"";width:7px;height:7px;border-radius:50%;border:1px solid #d9d9d9}
.contact-list{list-style:none;margin-top:14px}
.contact-list li{display:flex;gap:10px;font-size:10px;line-height:18px;align-items:flex-start;margin-bottom:11px}
.contact-list li::before{display:none}
.c-icon{flex:none;width:22px;height:22px;border-radius:50%;background:#efefef;display:flex;align-items:center;justify-content:center}

/* bottom bar */
.bottom-bar{top:2384px;height:65px;background:var(--red);color:var(--white)}
.social{position:absolute;left:162px;top:18px;display:flex;gap:8px}
.social span{width:29px;height:29px;border-radius:50%;border:1px solid var(--white)}
.copyright{position:absolute;left:784px;top:25px;font-size:10.5px;white-space:nowrap}
.copyright b{font-weight:400;margin-left:40px}
</style>
</head>
<body>

<header class="site-header">
  <div class="brand">Marigold Law<small>P.C</small></div>
  <nav class="main-nav">
    <a class="active" href="#" style="left:387px">Home</a>
    <a href="#" style="left:462px">Attorney Profile</a>
    <a href="#" style="left:591px">Practice Areas</a>
    <a href="#" style="left:713px">Client Reviews</a>
    <a href="#" style="left:836px">Links</a>
    <a href="#" style="left:908px">Contact Us</a>
  </nav>
  <div class="search-btn">
    <svg width="34" height="34" viewBox="0 0 34 34"><circle cx="16" cy="16" r="5" fill="none" stroke="#fff" stroke-width="2"/><line x1="19.5" y1="19.5" x2="23" y2="23" stroke="#fff" stroke-width="2.4" stroke-linecap="round"/></svg>
  </div>
</header>

<section class="hero">
  <div class="hero-photo" role="img" aria-label="Photo of attorneys and clients in a meeting around a conference table"></div>
  <div class="hero-content">
    <h1>Welcome to Marigold Law</h1>
    <p>Sed ut perspiciatis unde omnis iste natus sit voluptatem ac<br>cusantium dold ut perspiciatis unde omniorem.</p>
    <a class="btn" href="#">Request a Quote</a>
  </div>
  <div class="slider-dots"><span></span><span class="off"></span><span></span><span></span></div>
</section>

<section class="practice">
  <h2 class="section-title">PRACTICE AREAS</h2>
  <div class="title-rule"></div>
  <p class="practice-intro">Sed ut perspiciatis unde omnis iste natus error sit voluptatem accusantium doloremque laudantium, totam rem aperiam, eaque ipsa quae ab illo inventore veritatis et quasi architecto beatae vitae dicta sunt explicabo enim ipsam voluptatem quia voluptas sit aspernatur</p>

  <div class="area" style="left:151px">
    <svg class="area-icon" width="134" height="142" viewBox="0 0 134 142">
      <path d="M67 3a64 64 0 0 1 10 127l-10 11l-10-11A64 64 0 0 1 67 3z" fill="var(--red)"/>
      <circle cx="67" cy="67" r="58" fill="none" stroke="#fff" stroke-width="3"/>
      <rect x="42" y="72" width="8" height="18" fill="#fff"/><rect x="54" y="64" width="8" height="26" fill="#fff"/><rect x="66" y="56" width="8" height="34" fill="#fff"/><rect x="78" y="46" width="8" height="44" fill="#fff"/>
      <path d="M40 64l18-16l10 8l20-18" fill="none" stroke="#fff" stroke-width="4"/><path d="M82 34h12v12z" fill="#fff"/>
    </svg>
    <h3>Business Law</h3>
    <p>Sed ut perspiciatis unde omstusit voluptatem accusantium dolore ue lau dantium, totam rem aperiam.</p>
  </div>

  <div class="area" style="left:380px">
    <svg class="area-icon" width="134" height="142" viewBox="0 0 134 142">
      <path d="M67 3a64 64 0 0 1 10 127l-10 11l-10-11A64 64 0 0 1 67 3z" fill="var(--red)"/>
      <circle cx="67" cy="67" r="58" fill="none" stroke="#fff" stroke-width="3"/>
      <path d="M36 66l31-26l31 26" fill="none" stroke="#fff" stroke-width="5" stroke-linejoin="round"/>
      <path d="M45 62v28h44V62L67 44z" fill="#fff"/>
      <rect x="60" y="72" width="14" height="18" fill="var(--red)"/><rect x="50" y="66" width="8" height="8" fill="var(--red)"/><rect x="76" y="66" width="8" height="8" fill="var(--red)"/>
    </svg>
    <h3>Real Estate Law</h3>
    <p>Sed ut perspiciatis unde omstusit voluptatem accusantium dolore ue lau dantium, totam rem aperiam.</p>
  </div>

  <div class="area" style="left:610px">
    <svg class="area-icon" width="134" height="142" viewBox="0 0 134 142">
      <path d="M67 3a64 64 0 0 1 10 127l-10 11l-10-11A64 64 0 0 1 67 3z" fill="var(--red)"/>
      <circle cx="67" cy="67" r="58" fill="none" stroke="#fff" stroke-width="3"/>
      <circle cx="69" cy="40" r="8" fill="#fff"/>
      <ellipse cx="67" cy="70" rx="26" ry="18" fill="#fff"/>
      <rect x="52" y="82" width="7" height="12" fill="#fff"/><rect x="75" y="82" width="7" height="12" fill="#fff"/>
      <rect x="90" y="64" width="7" height="9" fill="#fff"/>
      <circle cx="80" cy="64" r="2.5" fill="var(--red)"/>
    </svg>
    <h3>Bankruptcy</h3>
    <p>Sed ut perspiciatis unde omstusit voluptatem accusantium dolore ue lau dantium, totam rem aperiam.</p>
  </div>

  <div class="area" style="left:839px">
    <svg class="area-icon" width="134" height="142" viewBox="0 0 134 142">
      <path d="M67 3a64 64 0 0 1 10 127l-10 11l-10-11A64 64 0 0 1 67 3z" fill="var(--red)"/>
      <circle cx="67" cy="67" r="58" fill="none" stroke="#fff" stroke-width="3"/>
      <circle cx="53" cy="50" r="8" fill="#fff"/><circle cx="81" cy="50" r="8" fill="#fff"/>
      <path d="M38 80c0-12 6-20 15-20s15 8 15 20z" fill="#fff"/><path d="M66 80c0-12 6-20 15-20s15 8 15 20z" fill="#fff"/>
      <circle cx="67" cy="66" r="7" fill="#fff" stroke="var(--red)" stroke-width="2"/>
      <path d="M54 92c0-10 6-16 13-16s13 6 13 16z" fill="#fff" stroke="var(--red)" stroke-width="2"/>
    </svg>
    <h3>Family Law</h3>
    <p>Sed ut perspiciatis unde omstusit voluptatem accusantium dolore ue lau dantium, totam rem aperiam.</p>
  </div>
</section>

<section class="about">
  <div class="about-media"><div role="img" aria-label="Word cloud of legal terms centred on criminal law"></div></div>
  <div class="about-text">
    <h2>MARIGOLD LAW, P.C.<br>ALDER CALIFORNIA ATTORNEY</h2>
    <hr>
    <p>Find the big firm style legal counsel you can work with in your hometown region at Marigold Law P.C., in Alder, CA. Attorney Dana L. Marigold, Esq., offers a boutique law firm opportunity for clients who want to enjoy all the advantages of her broad legal experience and education. She works closely with clients, and has the knowledge of many areas of law to apply to your situation. This is very helpful when it is necessary to incorporate those different areas of law practice into creating a winning argument for your unique case. Donec iaculis tempus magna, id rutrum sem commodo interdum. Interdum et malesuada fames ac ante ipsum primis in faucibunec iaculis tempus magna, id rutrum sem commodo interdum. Interdum et malesuada fames ac ante ipsum primis in faucibus.</p>
  </div>
</section>

<section class="blog">
  <h2 class="section-title">LATEST BLOG NEWS</h2>
  <div class="title-rule"></div>
  <div class="cards">
    <article class="post">
      <div class="post-thumb" role="img" aria-label="Photo of a team meeting around a table" style="background:linear-gradient(135deg,#c9b8a2,#7b6a5a 60%,#e0d8cc)"></div>
      <div class="post-body">
        <h3>Sed ut perspiciatis de omnis iste natus.</h3>
        <div class="post-meta"><span>&#9635; July 11,2016</span><span>&#9679; Admin</span></div>
        <p>Sed ut perspiciatis unde omnis isa tus error sit voluptatem accusa ntiu mdoloremque laudantium.</p>
        <a class="btn" href="#">Read More</a>
      </div>
    </article>
    <article class="post">
      <div class="post-thumb" role="img" aria-label="Photo of a judge's gavel on a wooden desk" style="background:linear-gradient(135deg,#5a3a28,#b48866 55%,#d8c2aa)"></div>
      <div class="post-body">
        <h3>Sed ut perspiciatis de omnis iste natus.</h3>
        <div class="post-meta"><span>&#9635; July 11,2016</span><span>&#9679; Admin</span></div>
        <p>Sed ut perspiciatis unde omnis isa tus error sit voluptatem accusa ntiu mdoloremque laudantium.</p>
        <a class="btn" href="#">Read More</a>
      </div>
    </article>
    <article class="post">
      <div class="post-thumb" role="img" aria-label="Photo of a lawyer working at a laptop" style="background:linear-gradient(135deg,#e8e8ea,#b7b4b2 55%,#6c5e56)"></div>
      <div class="post-body">
        <h3>Sed ut perspiciatis de omnis iste natus.</h3>
        <div class="post-meta"><span>&#9635; July 11,2016</span><span>&#9679; Admin</span></div>
        <p>Sed ut perspiciatis unde omnis isa tus error sit voluptatem accusa ntiu mdoloremque laudantium.</p>
        <a class="btn" href="#">Read More</a>
      </div>
    </article>
    <article class="post">
      <div class="post-thumb" role="img" aria-label="Photo of an attorney reading in a law library" style="background:linear-gradient(135deg,#3a2a20,#8a6440 55%,#c9a36e)"></div>
      <div class="post-body">
        <h3>Sed ut perspiciatis de omnis iste natus.</h3>
        <div class="post-meta"><span>&#9635; July 11,2016</span><span>&#9679; Admin</span></div>
        <p>Sed ut perspiciatis unde omnis isa tus error sit voluptatem accusa ntiu mdoloremque laudantium.</p>
        <a class="btn" href="#">Read More</a>
      </div>
    </article>
  </div>
</section>

<section class="partners" aria-label="Listings and memberships">
  <svg class="partner" style="left:364px;top:36px" width="60" height="56" viewBox="0 0 60 56"><circle cx="30" cy="26" r="24" fill="none" stroke="#2b4a7a" stroke-width="3"/><rect x="8" y="32" width="44" height="12" fill="#2b4a7a"/></svg>
  <svg class="partner" style="left:460px;top:34px" width="60" height="60" viewBox="0 0 60 60"><circle cx="30" cy="30" r="27" fill="none" stroke="#444" stroke-width="2"/><circle cx="30" cy="30" r="19" fill="none" stroke="#444" stroke-width="1.5"/></svg>
  <svg class="partner" style="left:548px;top:52px" width="106" height="24" viewBox="0 0 106 24"><rect x="0" y="2" width="106" height="14" fill="#1e3a6a"/><rect x="10" y="19" width="86" height="3" fill="#8a9ab8"/></svg>
  <svg class="partner" style="left:686px;top:48px" width="156" height="34" viewBox="0 0 156 34"><rect x="0" y="2" width="156" height="20" fill="#222"/><rect x="40" y="27" width="76" height="3" fill="#888"/></svg>
</section>

<footer class="site-footer">
  <div class="foot-brand">Marigold Law<small>P.C</small></div>
  <p class="foot-about">Sed ut perspiciatis unde omnis iste natus error sit voluptatem accu san tium doloremque laudantium, totam rem aperiam, eaque ipsa qu</p>

  <div class="foot-col" style="left:438px">
    <h4>Menu</h4>
    <ul><li>Home</li><li>Attorney Profile</li><li>Practice Areas</li><li>Client Reviews</li><li>Links</li><li>Contact Us</li></ul>
  </div>

  <div class="foot-col" style="left:622px">
    <h4>Links</h4>
    <ul><li>Business Law</li><li>Real Estate Law</li><li>Bankruptcy</li><li>Family Law</li><li>Criminal Law</li><li>Civil Litigation</li><li>Unlawful Detainer</li></ul>
  </div>

  <div class="foot-col" style="left:808px;width:260px">
    <h4>Contact Us</h4>
    <ul class="contact-list">
      <li><span class="c-icon"><svg width="12" height="12" viewBox="0 0 12 12"><path d="M2 1l2.5 0 1 3-1.5 1a7 7 0 0 0 3 3l1-1.5 3 1V10c0 .6-.5 1-1 1A9 9 0 0 1 1 2c0-.5.4-1 1-1z" fill="#333"/></svg></span><span style="padding-top:2px">Call Us (555) 014-2290</span></li>
      <li><span class="c-icon"><svg width="12" height="12" viewBox="0 0 12 12"><path d="M6 0a4 4 0 0 1 4 4c0 3-4 8-4 8S2 7 2 4a4 4 0 0 1 4-4z" fill="#333"/><circle cx="6" cy="4" r="1.5" fill="#efefef"/></svg></span><span style="white-space:nowrap">Marigold Law, P.C. Office 480 Elm Street,<br>Suite 200 Alder, CA 95000</span></li>
      <li><span class="c-icon"><svg width="12" height="12" viewBox="0 0 12 12"><rect x="1" y="4" width="10" height="6" fill="#333"/><rect x="3" y="1" width="6" height="3" fill="#333"/></svg></span><span style="padding-top:2px">Fax: (555) 014-2291</span></li>
      <li><span class="c-icon"><svg width="12" height="12" viewBox="0 0 12 12"><rect x="1" y="3" width="10" height="7" fill="#333"/><path d="M1 3l5 4 5-4" fill="none" stroke="#efefef"/></svg></span><span style="padding-top:2px">Email:dana@marigoldlawgroup.com</span></li>
    </ul>
  </div>
</footer>

<section class="bottom-bar">
  <div class="social" aria-label="Social links"><span></span><span></span><span></span><span></span></div>
  <p class="copyright">&copy; 2016 Marigold Law, P.C.. All copyrights are reserved.<b>C4</b></p>
</section>

</body>
</html>
```